Create the Hero Image for a Classic Rock Documentary Pledgemint

Create the Key Art & Visual Identity for a Classic Rock Documentary Pledgemint
Project Overview

I'm preparing to launch a Pledgemint campaign for an ambitious documentary-style music project unlike anything I've seen before.

Over approximately 700 hours, I am systematically listening to the complete pre-1990 studio catalogs of 29 classic rock bands—316 albums in total. Every album receives three complete listens, detailed written commentary, numerical scoring, and is entered into a custom-built database before I determine my final rankings.

This is not a reaction channel.

It is not a "Top 10" list built from memory or nostalgia.

It is a documented investigation built on discipline, repetition, curiosity, and evidence.

The project's title has not yet been finalized, so this contest is not about designing a logo or complete brand identity. Instead, I am looking for the defining visual image that introduces the entire project to the world.

The Assignment

Design the key art for my Pledgemint campaign.

This image will become the visual centerpiece of the campaign and will likely be adapted for:

Pledgemint campaign
Vidoria banner
Social media
Posters
Printed promotional material
Future merchandise

Think of this as creating the movie poster for a documentary rather than a Vidoria thumbnail.

Creative Direction

I am looking for an image that communicates:

commitment
curiosity
discovery
obsession
thoughtful listening
the journey behind the rankings

The project is ultimately about earning an opinion through disciplined listening rather than simply having one.

The visual should feel cinematic, timeless, intelligent, and memorable.

I prefer subtle storytelling over obvious symbolism.

One of the defining visual elements of the project is an inexpensive portable suitcase-style record player. Its simplicity is intentional. The project isn't about expensive audio equipment or audiophile culture—it is about disciplined listening. A notebook, over-ear headphones, handwritten notes, and vinyl records are all appropriate visual elements if they help tell the story.

The image should communicate that ordinary tools—a portable record player, headphones, a notebook, and hundreds of hours of disciplined listening—can become the foundation of an extraordinary investigation.

Photography

The uploaded photographs are reference images only. They introduce me as the subject of the documentary and illustrate the walking and travel that have become part of the project's story.

Walking has become an important part of how I experience music, think through ideas, and visit places connected to classic rock history.

If your concept is selected, I will gladly create new photography—with the appropriate clothing, props, portable record player, headphones, notebook, and poses—to fully realize your vision.

Please judge the project primarily on the strength of the creative concept rather than the supplied photographs.

Setting

The environment should feel authentic to the project's story.

Possible themes include:

long-distance travel
iconic music locations
record collecting
discovery
listening
investigation
classic rock history
the personal journey behind the project

The setting should support the narrative rather than simply provide an attractive background.

Design Style

I gravitate toward sophisticated editorial design rather than loud commercial graphics.

Imagine something that could serve as the poster for a feature documentary.

Elegant typography.

Strong composition.

Atmosphere.

Restraint.

The image should make someone stop, look a second time, and ask:

"What is this project?"

Deliverables

Please submit:

One primary hero image
Any supporting concept notes that help explain your vision

Placeholder typography is perfectly acceptable.

The emphasis is on concept, storytelling, and visual impact—not polished production.

Future Opportunity

The winning designer will be invited to quote on a larger body of work for the same project, including:

Pledgemint graphics
Vidoria banner
Posters
Gatefold album package
Postcards
Certificates
PDF layouts
Additional promotional materials

I'm looking for a designer who can become the long-term visual partner for this project, not simply someone to complete a single assignment.
Updates

Authenticity is extremely important for this project. The audience for this documentary values craftsmanship and can be skeptical of artwork that has an obvious AI-generated appearance. Whatever tools you choose to use, the finished image should feel authentic, believable, and professionally crafted. Please avoid the common visual artifacts and overly polished, synthetic aesthetic often associated with AI imagery. The final artwork should feel like it was created by a graphic artist making thoughtful creative decisions, not generated by a machine.

Target Market(s)

Music lovers ages 35–70, classic rock fans, vinyl collectors, documentary viewers, Vidoria audiences, and Pledgemint backers who appreciate thoughtful long-form storytelling rather than clickbait.

Industry/Entity Type

Entertainment / Documentary / Vidoria / Music

Font styles to use
Serif

Requirements
Must have
• The image should immediately communicate that this is a serious, thoughtful music project. The central character should be me (reference photos attached). I should appear focused and deeply engaged in listening to music. Include a small, inexpensive portable record player with a vinyl record. Include over-ear headphones. The scene should create a subtle visual contradiction: an obsessive listener using humble equipment. The environment should tell a story and encourage viewers to look more closely. The artwork should be cinematic and suitable for use as Vidoria channel art and Pledgemint promotional material.
Nice to have
• Surprise me with an original environment that reflects discovery, travel, history, or music culture. The setting does not need to be realistic if it creates a compelling visual story. Strong use of lighting, atmosphere, depth, and composition. Hidden visual details that reward a second look. A design style that could become the visual identity for an entire documentary project.
Should not have
• No guitars, microphones, stages, amplifiers, or performing musicians. No generic recording studios. No DJ equipment. No stereotypical rock imagery (flames, skulls, leather jackets, electric guitars, etc.). Do not make the record player look expensive or luxurious. Avoid clutter. Avoid cartoon or comic-book styles.

```html
<!DOCTYPE html>
<html lang="en">
<head>
<meta charset="utf-8">
<title>Classic Rock Documentary – Campaign Key Art</title>
<link href="https://fonts.googleapis.com/css2?family=Inter:wght@400;500;600&family=Jost:wght@500;600&family=Staatliches&display=swap" rel="stylesheet">
<style>
  :root{
    --paper:#f0e6d2;
    --parchment:#ece6da;
    --label:#f3dfb8;
    --rust:#6b2e0c;
    --charcoal:#3d3b39;
    --ink:#2b2b2b;
    --muted:#6f6f6f;
    --line:#e3e1dd;
    --page:#fafaf8;
    --band:#f3f1ec;
    --green:#05ce78;
    --button:#037d4c;
    --photo-top:#a9b3bd;
    --photo-mid:#7d8791;
    --photo-low:#6a6660;
  }
  *{box-sizing:border-box;margin:0;padding:0}
  html,body{width:1037px;height:1200px;overflow:hidden;background:#fff}
  body{position:relative;font-family:"Inter",sans-serif;color:var(--ink)}

  /* ---------- key art ---------- */
  .key-art{position:absolute;width:973px;height:551px;overflow:hidden;font-family:"Jost",sans-serif}
  .key-art--hero{left:32px;top:34px}
  .collage{position:absolute;inset:0;
    background:
      linear-gradient(90deg,transparent 61%,#8a5a2e 61%,#a06d3c 70%,transparent 70%) top/100% 62% no-repeat,
      radial-gradient(ellipse at 35% 55%,#ead39f 0%,#dcc08a 40%,transparent 70%),
      linear-gradient(120deg,#e6dfcf 0%,#e9cf98 40%,#d6b57a 70%,#c9a06a 100%)}
  .torn-field{position:absolute;inset:0;width:100%;height:100%}
  .subject-photo{position:absolute;left:196px;top:8px;width:206px;height:543px;
    border:6px solid var(--paper);border-bottom:none;border-radius:10px 10px 0 0;
    background:linear-gradient(180deg,var(--photo-top) 0%,var(--photo-mid) 45%,var(--photo-low) 100%)}
  .tag{position:absolute;background:var(--label);color:var(--rust);text-align:center;font-weight:600;text-transform:uppercase;box-shadow:0 1px 3px rgba(0,0,0,.15)}
  .tag--stats{left:423px;top:1px;width:190px;height:101px;padding-top:14px;font-size:12.6px;line-height:13.4px}
  .tag--stats small{display:block;margin-top:10px;font-size:9.2px;line-height:10px;color:#5b3a1c;font-weight:500}
  .tag--journey{left:0;top:362px;width:202px;height:125px;padding-top:15px;font-size:12.6px;line-height:14.4px}
  .tag--journey strong{display:block;margin-top:13px;font-size:15.4px;line-height:17px;color:var(--charcoal);font-weight:500}
  .headline{position:absolute;right:20px;top:245px;text-align:right;text-transform:uppercase}
  .headline__kicker{font-size:18.5px;line-height:23px;font-weight:600;color:var(--rust)}
  .headline__title{font-family:"Staatliches",sans-serif;font-size:60px;line-height:58px;color:var(--charcoal);margin-top:8px;letter-spacing:1px;font-weight:400}
  .headline__name{font-size:39px;line-height:46px;font-weight:600;color:var(--rust);margin-top:4px}

  /* ---------- campaign page ---------- */
  .preview-bar{position:absolute;left:38px;top:610px;font-size:7px;display:flex;align-items:center;gap:6px}
  .brand{font-family:"Inter",sans-serif;font-weight:600;color:var(--green);font-size:10px}
  .preview-bar a{color:#037d4c}
  .rule{position:absolute;left:35px;width:975px;height:1px;background:var(--line)}
  .page-body{position:absolute;left:32px;top:638px;width:973px;height:328px;background:var(--page)}
  .campaign-title{position:absolute;left:0;width:1037px;top:657px;text-align:center;font-size:12px;font-weight:600}
  .campaign-sub{position:absolute;left:0;width:1037px;top:675px;text-align:center;font-size:9px}
  .preview-frame{position:absolute;left:340px;top:704px;width:398px;height:226px;border:1px solid #333;overflow:hidden}
  .preview-frame .key-art{left:0;top:0;transform:scale(.408);transform-origin:0 0}
  .meta{position:absolute;left:341px;top:935px;display:flex;gap:12px;font-size:6px;align-items:center}
  .meta span{display:flex;align-items:center;gap:3px}
  .stats{position:absolute;left:752px;top:707px;width:189px}
  .progress{height:3px;background:#e8e8e6}
  .stat-num{font-size:13px;font-weight:500;margin-top:9px}
  .stat-num--big{font-size:14px;font-weight:600;color:#222}
  .stat-label{font-size:6.6px;color:var(--muted)}
  .back-btn{margin-top:13px;height:22px;background:var(--button);color:#fff;font-size:8px;display:flex;align-items:center;justify-content:center}
  .actions{display:flex;align-items:center;gap:9px;margin-top:8px}
  .remind{width:92px;height:20px;border:1px solid #ddd;background:#fff;font-size:6.5px;display:flex;align-items:center;justify-content:center;gap:4px}
  .share{width:11px;height:11px;border-radius:50%;background:#333}
  .fine{font-size:5.6px;color:#444;margin-top:9px;line-height:8px}
  .fine u{font-weight:500}
  .trust-band{position:absolute;left:32px;top:966px;width:973px;height:82px;background:var(--band)}
  .trust{position:absolute;top:990px;display:flex;gap:8px;font-size:8.6px;line-height:11.5px;width:190px}
  .trust i{flex:0 0 18px;height:18px;border-radius:5px}
  .tabs{position:absolute;left:342px;top:1055px;display:flex;gap:22px;font-size:6.6px}
  .tabs .off{color:#aaa}
  .tabs .on{font-weight:600;position:relative}
  .tabs .on::after{content:"";position:absolute;left:-2px;right:-2px;top:15px;height:2px;background:#333}
  .risks{position:absolute;left:346px;top:1099px;font-size:6.5px;font-weight:600}
  .story{position:absolute;left:450px;top:1098px;font-size:15px;font-weight:400}
  .support{position:absolute;left:763px;top:1101px;font-size:10.5px;font-weight:400}
  .pledge-box{position:absolute;left:764px;top:1127px;width:161px;height:60px;border:1px solid #e2e2e2;border-bottom:none;padding:8px}
  .pledge-box p{font-size:8.6px}
  .pledge-box small{display:block;margin-top:14px;font-size:6px}
</style>
</head>
<body>

<section class="key-art key-art--hero">
  <div class="collage" role="img" aria-label="Collage of aged handwritten letters, ledgers, postal stamps and a sketched hand holding a quill"></div>
  <svg class="torn-field" viewBox="0 0 973 551" preserveAspectRatio="none" aria-hidden="true">
    <path d="M973 0 L945 40 L900 110 L860 130 L790 190 L740 235 L700 260 L650 300 L625 340 L600 390 L560 420 L540 450 L560 500 L545 551 L973 551 Z" fill="var(--parchment)"/>
  </svg>
  <div class="subject-photo" role="img" aria-label="Cut-out photograph of the host walking with a hiking backpack"></div>

  <div class="tag tag--stats">700 Hours<br>29 Classic Rock Bands<br>316 Albums<small>A deep dive into the complete<br>pre-1990 studio catalogs</small></div>
  <div class="tag tag--journey">XX Miles Walked<br>XX Stories Uncovered<strong>Music and<br>experience that<br>will last lifetime</strong></div>

  <div class="headline">
    <p class="headline__kicker">A careful documentation<br>of the music that<br>shaped a generation</p>
    <h1 class="headline__title">Classic Rock<br>Documentary</h1>
    <p class="headline__name">Title Name<br>Placeholder</p>
  </div>
</section>

<div class="preview-bar"><span class="brand">Pledgemint</span><a href="#">Enable sharing</a><span>to send this preview to others and gather feedback.</span></div>
<div class="rule" style="top:637px"></div>
<div class="page-body"></div>

<h2 class="campaign-title">700 Hours, 29 Bands, 1 Database.</h2>
<p class="campaign-sub">The albums that raised us, finally put to the test.</p>

<div class="preview-frame">
  <section class="key-art">
    <div class="collage" role="img" aria-label="Collage of aged handwritten letters, ledgers, postal stamps and a sketched hand holding a quill"></div>
    <svg class="torn-field" viewBox="0 0 973 551" preserveAspectRatio="none" aria-hidden="true">
      <path d="M973 0 L945 40 L900 110 L860 130 L790 190 L740 235 L700 260 L650 300 L625 340 L600 390 L560 420 L540 450 L560 500 L545 551 L973 551 Z" fill="var(--parchment)"/>
    </svg>
    <div class="subject-photo" role="img" aria-label="Cut-out photograph of the host walking with a hiking backpack"></div>
    <div class="tag tag--stats">700 Hours<br>29 Classic Rock Bands<br>316 Albums<small>A deep dive into the complete<br>pre-1990 studio catalogs</small></div>
    <div class="tag tag--journey">XX Miles Walked<br>XX Stories Uncovered<strong>Music and<br>experience that<br>will last lifetime</strong></div>
    <div class="headline">
      <p class="headline__kicker">A careful documentation<br>of the music that<br>shaped a generation</p>
      <p class="headline__title">Classic Rock<br>Documentary</p>
      <p class="headline__name">Title Name<br>Placeholder</p>
    </div>
  </section>
</div>

<div class="meta">
  <span><svg width="8" height="8" viewBox="0 0 8 8"><circle cx="4" cy="4" r="3.3" fill="none" stroke="#333" stroke-width="1"/><path d="M2.6 5.4 L3.4 3.4 L5.4 2.6 L4.6 4.6Z" fill="#333"/></svg>Documentary</span>
  <span><svg width="7" height="9" viewBox="0 0 7 9"><path d="M3.5 0.5 C5.3 0.5 6.5 1.8 6.5 3.4 C6.5 5.4 3.5 8.5 3.5 8.5 C3.5 8.5 0.5 5.4 0.5 3.4 C0.5 1.8 1.7 0.5 3.5 0.5Z" fill="#333"/><circle cx="3.5" cy="3.4" r="1.1" fill="#fff"/></svg>Alder Creek, CA</span>
</div>

<aside class="stats">
  <div class="progress"></div>
  <p class="stat-num stat-num--big">$0</p>
  <p class="stat-label">pledged of $5,000 goal</p>
  <p class="stat-num">0</p>
  <p class="stat-label">backers</p>
  <p class="stat-num">30</p>
  <p class="stat-label">days to go</p>
  <div class="back-btn">Back this project</div>
  <div class="actions">
    <div class="remind"><svg width="6" height="7" viewBox="0 0 6 7"><path d="M0.7 0.5 H5.3 V6.5 L3 5 L0.7 6.5Z" fill="none" stroke="#333" stroke-width=".8"/></svg>Remind me</div>
    <span class="share"></span><span class="share"></span><span class="share"></span>
    <svg width="11" height="9" viewBox="0 0 11 9"><rect x=".5" y=".5" width="10" height="8" fill="none" stroke="#333"/><path d="M.5 .5 L5.5 5 L10.5 .5" fill="none" stroke="#333"/></svg>
    <svg width="11" height="9" viewBox="0 0 11 9"><rect x=".5" y=".5" width="10" height="8" rx="1" fill="none" stroke="#333"/><path d="M4 3 L2.5 4.5 L4 6 M7 3 L8.5 4.5 L7 6" fill="none" stroke="#333" stroke-width=".8"/></svg>
  </div>
  <p class="fine"><u>All or nothing.</u> This project will only be funded if it reaches its goal by the campaign deadline.</p>
</aside>

<div class="trust-band"></div>
<div class="trust" style="left:341px"><i role="img" aria-label="Connection illustration" style="background:#8a7df0"></i><span>Pledgemint connects creators with backers to fund projects.</span></div>
<div class="trust" style="left:547px"><i role="img" aria-label="Updates illustration" style="background:#f5d300"></i><span>Rewards aren’t guaranteed, but creators must regularly update backers.</span></div>
<div class="trust" style="left:752px"><i role="img" aria-label="Payment illustration" style="background:#2bc48a"></i><span>You’re only charged if the project meets its funding goal by the campaign deadline.</span></div>

<div class="rule" style="top:1048px;background:#ebe9e4"></div>
<nav class="tabs"><span class="on">Campaign</span><span>Rewards</span><span>Creator</span><span>FAQ</span><span class="off">Updates</span><span class="off">Comments</span><span class="off">Community</span></nav>
<div class="rule" style="top:1075px"></div>

<p class="risks">Risks</p>
<h2 class="story">Story</h2>
<h3 class="support">Support</h3>
<div class="pledge-box"><p>Make a pledge without a reward</p><small>Pledge amount</small></div>

</body>
</html>
```